Design a card that will be used for an e-gift card sold to customers.

I need to design the front an e-gift card for my pizza store. I picked the business card because it fits the same size as an e-gift card. I need the design and then I will submit to e-gift card company to produce. Looking for a fresh look that will appear cool, trendy to customer. Prefer to keep it to black and white but can add a bright green color.

Target Market(s)

My pizza store customers

Industry/Entity Type

Business

Contact Information for Business Card

I want the name Golden Hearth Pizza

Font styles to use
Sans Serif

Colors
9bcb3c

Requirements
Must have
• Golden Hearth Pizza
• Cedar Hollow
Nice to have
• I would like a black background. Maybe Golden Hearth Pizza in white and the location, Cedar Hollow. Maybe faded in background are words like, pizza, salads, wings, pepperoni, etc...or cartoon type pictures like pizza slices, fun pics. Would like to keep black and white shades but other colors are lighter greens.

```html
<!DOCTYPE html>
<html lang="en">
<head>
<meta charset="utf-8">
<title>Golden Hearth Pizza – E-Gift Card</title>
<link rel="stylesheet" href="https://fonts.googleapis.com/css2?family=Oswald:wght@400&family=Open+Sans:wght@400&display=swap">
<style>
  :root {
    --stage: #7d7d7d;
    --card: #1d1b1c;
    --white: #ffffff;
    --green: #9bcb3c;
    --rule: #bdbdbd;
    --faint: rgba(255, 255, 255, 0.05);
  }
  * { margin: 0; padding: 0; box-sizing: border-box; }
  html, body {
    width: 1200px;
    height: 900px;
    overflow: hidden;
    background: var(--stage);
  }
  .stage {
    width: 1200px;
    height: 900px;
    display: flex;
    align-items: center;
    justify-content: center;
  }
  .gift-card {
    position: relative;
    width: 900px;
    height: 555px;
    background: var(--card);
    border-radius: 0 100px 0 100px;
    overflow: hidden;
  }
  .slice-art {
    position: absolute;
    left: 218px;
    top: 87px;
    width: 558px;
    height: 353px;
    background: radial-gradient(ellipse at 60% 55%, var(--faint), transparent 70%);
  }
  .business-name {
    position: absolute;
    left: 0;
    right: 0;
    top: 168px;
    text-align: center;
    font-family: "Oswald", sans-serif;
    font-weight: 400;
    font-size: 76px;
    line-height: 1.2;
    letter-spacing: 2px;
    color: var(--green);
    text-transform: uppercase;
    white-space: nowrap;
  }
  .divider {
    position: absolute;
    left: 186px;
    width: 528px;
    top: 346px;
    height: 2px;
    background: var(--rule);
  }
  .location {
    position: absolute;
    left: 0;
    right: 0;
    top: 428px;
    display: flex;
    justify-content: center;
    align-items: center;
    gap: 16px;
    font-family: "Open Sans", sans-serif;
    font-size: 42px;
    line-height: 1.2;
    color: var(--white);
  }
  .location-pin { width: 28px; height: 42px; flex: none; }
</style>
</head>
<body>
  <main class="stage">
    <section class="gift-card">
      <div class="slice-art" role="img" aria-label="Faint outline drawing of a pizza slice in the background"></div>

      <h1 class="business-name">Golden Hearth Pizza</h1>

      <div class="divider"></div>

      <p class="location">
        <svg class="location-pin" viewBox="0 0 28 42" aria-hidden="true">
          <path d="M14 0C6.3 0 0 6.2 0 13.9 0 24.4 14 42 14 42s14-17.6 14-28.1C28 6.2 21.7 0 14 0z" fill="#9bcb3c"/>
          <circle cx="14" cy="14" r="5.5" fill="#1d1b1c"/>
        </svg>
        <span>Cedar Hollow</span>
      </p>
    </section>
  </main>
</body>
</html>
```